Brightfen Business Card Redesign & Logo Update

We need to update our business cards to something more modern and fresh. Brightfen can provide the current color schemes and old design examples, but welcome creativity in helping us with this redesign. PLEASE NOTE that we no longer utilize the "tree" and/or "leaf" imagery in our branding. If able would apprecaite an update on the quality of our "words only" logo in Ai. / PNG formats too.

Target Market(s)

Investors, landowners, corporate partners, contractors

Industry/Entity Type

Environmental Restoration & Conservation

Contact Information for Business Card

Logo, persons name, title, mailing address, phone and email, website url

Font styles to use
Other font styles liked:
• Merriweather

Requirements
Nice to have
• Logo, persons name, title, mailing address, phone and email, website url, but open to ideams
Should not have
• No all back backgrounds

```html
<!DOCTYPE html>
<html lang="en">
<head>
<meta charset="utf-8">
<title>Brightfen Business Card</title>
<link href="https://fonts.googleapis.com/css2?family=Open+Sans:wght@400;700;800&display=swap" rel="stylesheet">
<style>
  :root {
    --bg: #e6e7e9;
    --card: #ffffff;
    --green: #138040;
    --orange: #ee7f22;
    --ink: #1a1a1a;
    --white: #ffffff;
  }
  * { margin: 0; padding: 0; box-sizing: border-box; }
  html, body { width: 1200px; height: 780px; overflow: hidden; }
  body {
    background: var(--bg);
    font-family: "Open Sans", Arial, sans-serif;
    position: relative;
  }
  .card {
    position: absolute;
    width: 560px;
    height: 320px;
    background: var(--card);
    border-radius: 22px;
    overflow: hidden;
    box-shadow: 0 6px 18px rgba(0,0,0,0.18);
  }
  .card--front { left: 50px; top: 60px; }
  .card--back { left: 590px; top: 400px; }

  .wordmark { position: absolute; }
  .wordmark__name {
    display: block;
    font-weight: 800;
    color: var(--green);
    text-transform: uppercase;
    line-height: 1;
    letter-spacing: 1px;
  }
  .wordmark__tagline {
    display: block;
    font-weight: 700;
    color: var(--ink);
    text-transform: uppercase;
    letter-spacing: 0.5px;
    margin-top: 4px;
  }
  .card--front .wordmark { left: 50%; top: 50%; transform: translate(-50%, -50%); text-align: left; }
  .card--front .wordmark__name { font-size: 78px; }
  .card--front .wordmark__tagline { font-size: 22.5px; }

  .card--back .wordmark { left: 28px; top: 36px; }
  .card--back .wordmark__name { font-size: 44px; }
  .card--back .wordmark__tagline { font-size: 12.7px; margin-top: 2px; }

  .card__art { position: absolute; inset: 0; }

  .holder {
    position: absolute;
    right: 34px;
    top: 28px;
    text-align: right;
  }
  .holder__name { font-weight: 700; font-size: 21px; color: var(--ink); }
  .holder__title { font-weight: 400; font-size: 12px; color: var(--ink); margin-top: 1px; }

  .contact {
    position: absolute;
    right: 22px;
    top: 176px;
    list-style: none;
    text-align: right;
  }
  .contact__item {
    display: flex;
    justify-content: flex-end;
    align-items: center;
    gap: 8px;
    color: var(--white);
    font-size: 14px;
    line-height: 22px;
  }
  .contact__icon { width: 13px; height: 13px; flex: none; }
</style>
</head>
<body>

<section class="card card--front">
  <div class="wordmark">
    <span class="wordmark__name">Brightfen</span>
    <span class="wordmark__tagline">Environmental Credit Company</span>
  </div>
</section>

<section class="card card--back">
  <svg class="card__art" viewBox="0 0 560 320" width="560" height="320" aria-hidden="true">
    <rect x="534" y="0" width="26" height="30" fill="var(--green)"/>
    <path d="M560 110 C470 110 420 140 380 220 C345 290 250 300 0 300 L0 320 L560 320 Z" fill="var(--green)"/>
    <path d="M470 120 C420 135 390 165 365 215 C330 280 240 290 0 290" fill="none" stroke="var(--orange)" stroke-width="5"/>
  </svg>

  <div class="wordmark">
    <span class="wordmark__name">Brightfen</span>
    <span class="wordmark__tagline">Environmental Credit Company</span>
  </div>

  <div class="holder">
    <p class="holder__name">Lena Marovic</p>
    <p class="holder__title">Managing Director</p>
  </div>

  <ul class="contact">
    <li class="contact__item">(555) 214-0376
      <svg class="contact__icon" viewBox="0 0 16 16"><path d="M3.5 1 L6 1 L7 4.5 L5.3 5.8 C6.2 7.7 8.3 9.8 10.2 10.7 L11.5 9 L15 10 L15 12.5 C15 14 13.8 15 12.5 15 C6.5 14.6 1.4 9.5 1 3.5 C1 2.2 2 1 3.5 1 Z" fill="var(--white)"/></svg>
    </li>
    <li class="contact__item">info@brightfen.com
      <svg class="contact__icon" viewBox="0 0 16 16"><rect x="1" y="3" width="14" height="10" rx="1" fill="var(--white)"/><path d="M1.5 3.8 L8 9 L14.5 3.8" fill="none" stroke="var(--green)" stroke-width="1.4"/></svg>
    </li>
    <li class="contact__item">www.brightfen.com
      <svg class="contact__icon" viewBox="0 0 16 16"><circle cx="8" cy="8" r="7" fill="var(--white)"/><path d="M1 8 H15 M8 1 C5 4 5 12 8 15 M8 1 C11 4 11 12 8 15" fill="none" stroke="var(--green)" stroke-width="1.1"/></svg>
    </li>
  </ul>
</section>

</body>
</html>
```